Business Card Design

I need business cards designed for a new company i have started that makes cakes, particularly themed kids cakes with a really modern design and I would like to have my business cards reflect this. I have attached some photos of cakes I have made and would like some to be used.

Industry/Entity Type

Business

Contact Information for Business Card

Business Name: Tarts and Treats by Maren
Mobile: 0492 815 063
email: maren@tartsandtreatsbymaren.example.au
Instagram: instagram.com/tartsandtreatsbymaren/
Facebook: fb.me/tartsandtreatsbymaren

Colors
e667a6
b768aa
3276b5

Requirements
Must have
• Business Name: Tarts and Treats by Maren
• Mobile: 0492 815 063
• email: maren@tartsandtreatsbymaren.example.au
• Instagram: instagram.com/tartsandtreatsbymaren/
• Facebook: fb.me/tartsandtreatsbymaren
Nice to have
• 2 to 3 pictures of my cakes

```html
<!DOCTYPE html>
<html lang="en">
<head>
<meta charset="utf-8">
<title>Tarts and Treats by Maren – Business Card</title>
<link rel="stylesheet" href="https://fonts.googleapis.com/css2?family=Open+Sans:wght@400;600;700&display=swap">
<style>
  :root {
    --backdrop: #ece8e4;
    --card-white: #ffffff;
    --brand-pink: #e667a6;
    --brand-pink-deep: #d4559a;
    --brand-plum: #b768aa;
    --brand-blue: #3276b5;
    --ink-on-pink: #ffffff;
    --rule-on-pink: rgba(255, 255, 255, 0.45);
    --shadow: rgba(60, 40, 30, 0.22);
  }
  * { box-sizing: border-box; margin: 0; padding: 0; }
  html, body {
    width: 1200px;
    height: 843px;
    overflow: hidden;
    background: var(--backdrop);
    font-family: "Open Sans", Arial, sans-serif;
  }
  .canvas {
    position: relative;
    width: 1200px;
    height: 843px;
    display: flex;
    align-items: center;
    justify-content: center;
    gap: 44px;
  }
  .card {
    width: 520px;
    height: 318px;
    border-radius: 4px;
    box-shadow: 0 14px 30px var(--shadow);
    position: relative;
    overflow: hidden;
  }

  /* Front: white with brand name */
  .card-front {
    background: var(--card-white);
    display: flex;
    align-items: center;
    justify-content: center;
  }
  .brand {
    display: flex;
    align-items: center;
    gap: 12px;
  }
  .brand-dot {
    width: 22px;
    height: 22px;
    border-radius: 50%;
    background: var(--brand-blue);
    flex: none;
  }
  .brand-name {
    font-weight: 600;
    font-size: 26px;
    color: var(--brand-pink);
    letter-spacing: 0.3px;
  }

  /* Back: pink with contact details */
  .card-back {
    background: linear-gradient(100deg, var(--brand-pink) 0%, var(--brand-pink-deep) 100%);
    color: var(--ink-on-pink);
    padding: 0 44px;
    display: flex;
    flex-direction: column;
    justify-content: center;
  }
  .holder {
    text-align: center;
    font-size: 20px;
    font-weight: 600;
    letter-spacing: 0.5px;
    margin-bottom: 14px;
  }
  .holder .role {
    font-size: 15px;
    font-weight: 400;
    letter-spacing: 0;
  }
  .rule {
    height: 1px;
    background: var(--rule-on-pink);
    width: 100%;
  }
  .contact {
    list-style: none;
    text-align: center;
    font-size: 14px;
    line-height: 1.7;
    margin-bottom: 12px;
  }
  .contact .label { font-weight: 700; }
  .social {
    display: flex;
    justify-content: center;
    gap: 12px;
    margin: 12px 0;
  }
  .social-mark {
    width: 26px;
    height: 26px;
    border-radius: 4px;
    background: var(--ink-on-pink);
    opacity: 0.9;
  }
</style>
</head>
<body>
  <main class="canvas">
    <section class="card card-front" aria-label="Card front">
      <div class="brand">
        <span class="brand-dot"></span>
        <span class="brand-name">Tarts and Treats by Maren</span>
      </div>
    </section>

    <section class="card card-back" aria-label="Card back">
      <p class="holder">JONAH PELL – <span class="role">CEO/Founder</span></p>
      <ul class="contact">
        <li><span class="label">Mob:</span> 0492 815 063</li>
        <li><span class="label">Email:</span> maren@tartsandtreatsbymaren.example.au</li>
      </ul>
      <div class="rule"></div>
      <div class="social" aria-label="Social profiles">
        <span class="social-mark" role="img" aria-label="Photo profile icon"></span>
        <span class="social-mark" role="img" aria-label="Social page icon"></span>
      </div>
      <div class="rule"></div>
    </section>
  </main>
</body>
</html>
```